Flyer-Design für Startup
Zielgruppe
Unser Unternehmen ist ein Startup in der Bildungslandschaft. Hinsichtlich dem Flyer besteht die Zielgruppe aus Studierenden im Alter zwischen 25 und 40 Jahren.
Aufgabenstellung
Die Texte sollten in der Vektor Datei bearbeitbare sein!
Die Frau im Feld sowie die Farben des Logos sollten im Flyer berücksichtigt werden. Zudem sollen die Inhalte auch grafisch aufgearbeitet werden. Format: Es soll ein 6-seitiger Zickzackfalz sein.
Unsere Webseite ist vorübergehend nur im Entwurfsmodus durch das Passwort 'lumacor4727' erreichbar.
Schriftart Helvetica!

```html
<!DOCTYPE html>
<html lang="de">
<head>
<meta charset="utf-8">
<title>Lumacor – Geprüfte/r Wirtschaftsfachwirt</title>
<link href="https://fonts.googleapis.com/css2?family=Arimo:wght@400;700&display=swap" rel="stylesheet">
<style>
:root{
  --navy:#0d2a4a;
  --blue:#1a8fd4;
  --olive:#8a8f1e;
  --red:#d0202e;
  --magenta:#c4257a;
  --orange:#e8701f;
  --rust:#d6461c;
  --bullet:#f0a21e;
  --ink:#2b2b2b;
  --panel-mid:#ececec;
  --panel-right:#f6f6f6;
}
*{margin:0;padding:0;box-sizing:border-box}
html,body{width:1200px;height:862px;overflow:hidden}
body{font-family:"Arimo",Helvetica,Arial,sans-serif;color:var(--ink);position:relative;background:#fff}
.panel{position:absolute;top:0;height:862px}
.panel-cover{left:0;width:414px;overflow:hidden}
.panel-mid{left:414px;width:388px;background:var(--panel-mid)}
.panel-right{left:802px;width:398px;background:var(--panel-right)}
.cover-photo{position:absolute;inset:0;background:
  radial-gradient(ellipse at 45% 62%,#ffd35c 0%,#f7a43a 22%,rgba(230,120,50,.6) 45%,transparent 70%),
  linear-gradient(180deg,#5b4a5e 0%,#b37358 18%,#e39a55 40%,#eea04a 60%,#8a5448 80%,#2f2637 100%)}
.brand{position:absolute;left:0;width:414px;top:145px;display:flex;justify-content:center;align-items:center;gap:10px}
.brand-square{width:26px;height:26px;background:var(--navy)}
.brand-name{font-size:34px;font-weight:700;color:var(--navy);letter-spacing:-.5px}
.cover-text{position:absolute;left:40px;width:334px;text-align:center;color:#fff;font-size:12.6px;line-height:16.4px}
.step{position:absolute;left:0;width:222px;height:76px;border-top:1.5px solid;border-bottom:1.5px solid;border-right:1.5px solid}
.step-circle{position:absolute;left:183px;width:75px;height:75px;border-radius:50%;background:rgba(255,240,215,.55);
  display:flex;align-items:center;justify-content:center;font-size:46px;font-weight:400}
.s1{border-color:var(--olive)} .c1{color:var(--olive)}
.s2{border-color:var(--blue)} .c2{color:var(--blue)}
.s3{border-color:var(--magenta)} .c3{color:var(--magenta)}
.block{position:absolute;font-size:12px;line-height:15.6px;letter-spacing:-.1px}
.mid{left:27px;width:348px}
.right{left:22px;width:352px}
.head{position:absolute;display:flex;align-items:center;gap:8px;font-size:16.5px;font-weight:700;left:4px}
.head svg{width:15px;height:24px}
.head span{margin-left:4px}
p+p{margin-top:6px}
ul{list-style:none}
li{position:relative;padding-left:20px;margin-bottom:6px}
li::before{content:"";position:absolute;left:1px;top:5px;width:6px;height:6px;border-radius:50%;background:var(--bullet)}
.pink li::before{background:#d06a8a}
.sub{font-size:14px;font-weight:700;color:var(--orange)}
.note{font-size:12.6px;font-weight:700;color:var(--olive);line-height:16.4px}
.footer-band{position:absolute;left:414px;top:797px;width:786px;height:65px;background:linear-gradient(90deg,#1c2236,#2d2a3c 60%,#3a3545)}
.footer-mark{position:absolute;left:0;top:0;width:57px;height:50px;background:var(--navy);color:#fff;font-size:9px;font-weight:700;display:flex;align-items:center;justify-content:center}
.footer-title{position:absolute;left:94px;top:14px;font-size:18px;color:#fff;letter-spacing:8.5px;white-space:nowrap}
.footer-title b{font-weight:400;margin-right:14px}
</style>
</head>
<body>

<section class="panel panel-cover">
  <div class="cover-photo" role="img" aria-label="Frau mit ausgestreckten Armen im Feld vor Sonnenuntergang"></div>
  <div class="brand"><span class="brand-square"></span><span class="brand-name">Lumacor</span></div>
  <div class="cover-text" style="top:197px">Aufbau unserer Kurse<br>Wir bieten Ihnen klare und einheitliche Lernunterlagen, die auf den aktuellen Rahmenplan der Industrie- und Handelskammer aufbauen. Hierdurch können wir eine intensive Prüfungsvorbereiten gewährleisten.</div>
  <div class="step s1" style="top:306px"></div>
  <div class="step-circle c1" style="top:307px">1</div>
  <div class="cover-text" style="top:394px">Theorievermittlung<br>Wir vermitteln Ihnen querschnittsübergreifend das prüfungsrelevante Wissen. Die Verknüpfung zwischen Theorie und Praxis vereinfacht den Prozess. Der Unterricht erfolgt in einem virtuellen Klassenzimmer.</div>
  <div class="step s2" style="top:486px"></div>
  <div class="step-circle c2" style="top:487px">2</div>
  <div class="cover-text" style="top:575px">Prüfungsvorbereitung<br>Wir zeigen Ihnen die komplette Bandbreite klausurähnlicher Übungsaufgabe. Hierdurch sind Sie auf unterschiedliche Szenarien vorbereitet.</div>
  <div class="step s3" style="top:651px"></div>
  <div class="step-circle c3" style="top:652px">3</div>
  <div class="cover-text" style="top:740px">Wir sind für Sie da<br>Profitieren Sie von unserem Bildungsnetzwerk und nutzen Sie Synergieeffekte. Wir unterstützen Sie bei Ihrer Karriereplanung.</div>
</section>

<section class="panel panel-mid">
  <div class="head" style="top:40px;color:var(--blue)"><svg viewBox="0 0 15 24"><path d="M0 0H15V24H0L6 12Z" fill="var(--blue)"/></svg><span>ZIELGRUPPE</span></div>
  <div class="block mid" style="top:78px">
    <p>Eine Aufstiegsfortbildung zum/zur Wirtschaftsfachwirt/-in vermittelt generalistisches Fachwissen im Bereich Handel, Industrie sowie Dienstleistungen und zählt insofern als Allrounder zu den populärsten Aufstiegsfortbildungen im kaufmännischen Bereich. Wirtschaftsfachwirte übernehmen in der Regel Führungsaufgaben und können betriebswirtschaftliche Zusammenhänge in ihrem Gesamtzusammenhang erkennen und beurteilen.</p>
  </div>
  <div class="block mid" style="top:218px">
    <p>Der Abschluss zum/zur Wirtschaftsfachwirt/-in ist eine echte Alternative zum klassischen Bachelorstudium an einer Hochschule. Der wesentliche Unterschied liegt in der praxisnahen Auslegung der Theorieinhalte. Mit der Zuordnung auf DQR-Stufe 6 befindet sich der Abschluss auf derselben Stufe wie die Bachelor-Abschlüsse der Hochschulen.</p>
  </div>
  <div class="head" style="top:326px;color:var(--olive)"><svg viewBox="0 0 15 24"><path d="M0 0H15V24H0L6 12Z" fill="var(--olive)"/></svg><span>ZIELSETZUNG</span></div>
  <div class="block mid" style="top:355px">
    <p>Dieser Kurs bereitet Sie auf die Prüfung zum/r geprüften Wirtschaftsfachwirt/in (IHK) vor.</p>
    <p>Die Anmeldung zur Prüfung bei der für Sie örtlich zuständigen Industrie- und Handelskammer erfolgt durch den Teilnehmer und die Prüfung ist innerhalb des Maßnahmenzeitraums abzulegen.</p>
  </div>
  <div class="head" style="top:469px;color:var(--red)"><svg viewBox="0 0 15 24"><path d="M0 0H15V24H0L6 12Z" fill="var(--red)"/></svg><span>KOSTEN</span></div>
  <div class="block mid" style="top:499px">
    <p>Die Maßnahme ist nach AZAV durch die Certivo als fachkundige Stelle zugelassen und erfüllt damit die Voraussetzung der Förderung über einen Bildungsgutschein durch die Agentur für Arbeit (SGB III) bzw. JobCenter (SGB II), durch Rentenversicherungsträger oder nach dem Soldatenversorgungsgesetz von bis 100 % der Kosten. Die lokalen Agenturen für Arbeit bzw. JobCenter, die Rentenversicherungsträger oder die Berufsförderungsdienste erteilen hierzu nähere Auskünfte</p>
  </div>
  <div class="head" style="top:638px;color:var(--magenta)"><svg viewBox="0 0 15 24"><path d="M0 0H15V24H0L6 12Z" fill="var(--magenta)"/></svg><span>IHR PERSÖNLICHER VORTEIL</span></div>
  <div class="block mid pink" style="top:667px">
    <ul>
      <li>Zeugnis des Trägers und/oder Teilnahmebescheinigung</li>
      <li>Bundesweit anerkannter IHK-Abschluss</li>
      <li>Querschnittsübergreifendes Fachwissen</li>
      <li>Qualifizierung zur Übernahme einer höheren Position</li>
    </ul>
    <p>Weiterqualifizierung zum Master Professional of Business Management (CCI) ist nach Erhalt des Abschlusses möglich</p>
  </div>
</section>

<section class="panel panel-right">
  <div class="head" style="top:40px;color:var(--rust);left:0"><svg viewBox="0 0 15 24"><path d="M0 0H15V24H0L6 12Z" fill="var(--rust)"/></svg><span>TEILNEHMERVORAUSSETZUNGEN</span></div>
  <div class="block right" style="top:70px">
    <div class="sub">Fachliche Voraussetzungen</div>
    <p style="margin:7px 0 6px">Für die Teilprüfung <b>„Wirtschaftsbezogene Qualifikationen“</b></p>
    <ul>
      <li>werden Sie zugelassen, wenn Sie eine erfolgreich bestandene Abschlussprüfung in einem anerkannten mindestens dreijährigen kaufmännischen <b>oder</b></li>
      <li>eine erfolgreich bestandene Abschlussprüfung in einem sonstigen anerkannten mindestens dreijährigen Ausbildungsberuf und danach mindestens ein Jahr Berufspraxis vorweisen können, <b>oder</b></li>
      <li>eine erfolgreich bestandene Abschlussprüfung in einem anderen anerkannten Ausbildungsberuf und danach mindestens zwei Jahre Berufspraxis gesammelt haben, <b>oder</b></li>
      <li>mindestens drei Jahre Berufspraxis vorweisen können.</li>
    </ul>
    <p style="margin-bottom:6px">Für die Teilprüfung <b>„Handlungsspezifische Qualifikationen“</b></p>
    <ul>
      <li>werden Sie zugelassen, wenn die abgelegte Teilprüfung „Wirtschaftsbezogene Qualifikationen“, nicht länger als fünf Jahre zurückliegt und Sie mindestens ein weiteres Jahr Berufspraxis zu den Zulassungsvoraussetzungen unter der Teilprüfung „Wirtschaftsbezogene Qualifikationen“ nachweisen können</li>
    </ul>
    <div class="note">Den Antrag auf Prüfung der Zulassungsvoraussetzungen erhalten Sie bei Ihrer zuständigen Industrie- und Handelskammer.</div>
    <div class="sub" style="margin-top:10px">Technische Voraussetzungen</div>
    <p style="margin:6px 0 10px">Für die Teilnahme an der Fortbildung benötigen Sie einen PC, der die folgenden Hardwareanforderungen für Systema-Systeme erfüllt:</p>
    <ul>
      <li>Computer und Prozessor: Mindestens 1,6 GHz (oder höher), 2-Core-Prozessor</li>
      <li>Arbeitsspeicher: 4,0 GB RAM</li>
      <li>Festplatte: 3,0 GB verfügbarer Speicherplatz</li>
      <li>Anzeige: Bildschirmauflösung von 1024 x 768 Pixel</li>
      <li>Grafikkarte: Grafikhardwarebeschleunigung erfordert GraphX 9 oder höher, mit SDDM 2.0 oder höher für Systema 10</li>
      <li>Betriebssystem: Systema 8</li>
      <li>Video: USB 2.0-Videokamera (oder interne Kamera)</li>
    </ul>
  </div>
</section>

<footer class="footer-band">
  <div class="footer-mark">Lumacor</div>
  <div class="footer-title"><b>GEPRÜFTE/R</b> WIRTSCHAFTSFACHWIRT</div>
</footer>

</body>
</html>
```